Garlic Farm for Farm Sales/Restaurant sales

Need a professional, but appealing to agriculture world. We are selling 27 kinds of Organic Garlic from a farm in Simla,CO. I have uploaded logo and business information-we are going to need a template, because I will need to use it for four separate people.
-We are trying to appeal to Farm to table restaurants
-As well as growers/farmers

Target Market(s)

Agriculture Sales/Restaurants-Organic

Industry/Entity Type

Agriculture

Contact Information for Business Card

Want it to look more unique then your average kelto stock card- I want it to look amazing

Font styles to use
Sans Serif

Colors
0455a3
ec1f27
fbed22
ffffff

Requirements
Must have
• Just be creative
Nice to have
• Colorful
Should not have
• plain

```html
<!DOCTYPE html>
<html lang="en">
<head>
<meta charset="utf-8">
<title>Ridgeline Garlic — Business Card</title>
<link href="https://fonts.googleapis.com/css2?family=Source+Sans+3:wght@400;600;700&display=swap" rel="stylesheet">
<style>
  :root {
    --stage: #000000;
    --card-light: #f3f3f3;
    --brand-red: #bd0a2a;
    --brand-red-deep: #9c0c2e;
    --brand-red-soft: #c81a34;
    --brand-navy: #1c2d5e;
    --brand-yellow: #fdd800;
    --corner: 62px;
  }
  * { margin: 0; padding: 0; box-sizing: border-box; }
  html, body {
    width: 1200px;
    height: 900px;
    overflow: hidden;
    background: var(--stage);
    font-family: "Source Sans 3", sans-serif;
  }
  .stage { position: relative; width: 1200px; height: 900px; }

  .card { position: absolute; top: 200px; height: 501px; }

  /* Front */
  .card-front {
    left: 265px;
    width: 310px;
    background: var(--card-light);
    border-radius: var(--corner) 0 var(--corner) 0;
  }
  .brand-mark {
    position: absolute;
    left: 50%;
    top: 46px;
    width: 92px;
    height: 92px;
    margin-left: -46px;
    border-radius: 50%;
    background: var(--brand-red);
  }
  .brand-name {
    position: absolute;
    left: 0;
    right: 0;
    top: 150px;
    text-align: center;
    font-size: 32px;
    font-weight: 700;
    line-height: 40px;
    color: var(--brand-navy);
  }

  .person { position: absolute; left: 38px; top: 276px; }
  .person-name {
    font-size: 20px;
    font-weight: 700;
    color: var(--brand-red);
    line-height: 23px;
  }
  .person-role {
    font-size: 14.5px;
    color: var(--brand-navy);
    line-height: 18px;
  }

  .address {
    position: absolute;
    left: 38px;
    top: 340px;
    font-size: 14.5px;
    line-height: 15.5px;
    color: var(--brand-navy);
    font-style: normal;
  }

  .contact-list {
    position: absolute;
    left: 38px;
    top: 385px;
    list-style: none;
  }
  .contact-list li {
    display: flex;
    align-items: center;
    height: 21px;
    font-size: 14.5px;
    color: var(--brand-navy);
  }
  .contact-icon {
    width: 10px;
    height: 10px;
    margin-right: 10px;
    fill: var(--brand-red);
    flex: none;
  }

  /* Back */
  .card-back {
    left: 641px;
    width: 308px;
    border-radius: 0 var(--corner) 0 var(--corner);
    overflow: hidden;
    background:
      radial-gradient(circle at 155px 225px,
        var(--brand-red) 0 150px,
        var(--brand-red-deep) 160px 172px,
        var(--brand-red-soft) 182px 200px,
        var(--brand-red) 212px);
  }
  .back-mark {
    position: absolute;
    left: 50%;
    top: 120px;
    width: 190px;
    height: 190px;
    margin-left: -95px;
    border-radius: 50%;
    background: var(--brand-yellow);
  }
  .back-name {
    position: absolute;
    left: 0;
    right: 0;
    top: 334px;
    text-align: center;
    font-size: 34px;
    font-weight: 700;
    line-height: 40px;
    color: var(--brand-yellow);
  }
</style>
</head>
<body>
<main class="stage">

  <section class="card card-front" aria-label="Business card front">
    <div class="brand-mark"></div>
    <div class="brand-name">Ridgeline Garlic</div>

    <div class="person">
      <p class="person-name">Daniel Hart</p>
      <p class="person-role">Managing Director</p>
    </div>

    <address class="address">
      12345, Address Goes Here<br>
      Country Name, 123456
    </address>

    <ul class="contact-list">
      <li>
        <svg class="contact-icon" viewBox="0 0 10 10" aria-hidden="true">
          <path d="M2 0.5 L3.6 2.6 L2.7 3.7 C3.3 5 4.8 6.6 6.3 7.3 L7.4 6.4 L9.5 8 L8.4 9.5 C4.5 9.2 0.8 5.5 0.5 1.6 Z"/>
        </svg>
        (044)-456-7890
      </li>
      <li>
        <svg class="contact-icon" viewBox="0 0 10 10" aria-hidden="true">
          <path d="M2.5 0.5 H7.5 V3 H9.5 V9.5 H0.5 V3 H2.5 Z M3.5 1.5 V3 H6.5 V1.5 Z M2 5 V6 H4 V5 Z M5 5 V6 H8 V5 Z M2 7 V8 H4 V7 Z M5 7 V8 H8 V7 Z" fill-rule="evenodd"/>
        </svg>
        123-456-7890
      </li>
      <li>
        <svg class="contact-icon" viewBox="0 0 10 10" aria-hidden="true">
          <path d="M0.5 2 H9.5 V8.5 H0.5 Z"/>
          <path d="M1 2.7 L5 5.9 L9 2.7" fill="none" stroke="#f3f3f3" stroke-width="0.8"/>
        </svg>
        info@youremail.com
      </li>
      <li>
        <svg class="contact-icon" viewBox="0 0 10 10" aria-hidden="true">
          <circle cx="5" cy="5" r="4.5"/>
          <path d="M5 0.8 V9.2 M0.8 5 H9.2 M5 0.8 C3 3 3 7 5 9.2 M5 0.8 C7 3 7 7 5 9.2" fill="none" stroke="#f3f3f3" stroke-width="0.7"/>
        </svg>
        www.website.com
      </li>
    </ul>
  </section>

  <section class="card card-back" aria-label="Business card back">
    <div class="back-mark"></div>
    <div class="back-name">Ridgeline Garlic</div>
  </section>

</main>
</body>
</html>
```